Larkspur Talent IT Recruiting firm needs a business card design for Recruiters, Sourcers, and Account

We need business cards that allow us to change all contact info, names, titles (Recruiter, Sourcer, Account Manager, Director, CEO, etc) per person since we have three offices, in three cities, Phoenix, Austin, and Las Vegas. We do recruiting and contractors for IT positions (Developers, Architects, Software Engineers, Security Engineers, Help Desk, DBAs, PMs, Scrum Masters, etc.) Our client companies are very diverse from Meridian 100 to silicone Valley type start-ups.

So, while we what hip, techie, and quirky, it still needs to be professional. Primary color we use is blue, with silver as a secondary color.

Target Market(s)

IT, Technology

Industry/Entity Type

Business

Contact Information for Business Card

Company name: Larkspur Talent, Inc.
Website: www.larkspurtalent.example
Logos for Careerloop, Blipster, and Myriada

Name, Title, Office Number, Cell Number, email

Font styles to use
Serif
Sans Serif

Colors
0455a3
d5d5d5

Requirements
Nice to have
• The grey I selected below is not necessary - but, would like silver included. I included a card design (File 3: LTI early trial example.jpg) that I had started on. It's very rough, and not quite what we're looking for, but what we did like is the logo, big, maybe a bit faded, off center, goes out of frame, etc. Still looking for other ideas - you are the pros! But, just an idea of a design element we liked.

```html
<!DOCTYPE html>
<html lang="en">
<head>
<meta charset="utf-8">
<title>Larkspur Talent – Business Card</title>
<link rel="stylesheet" href="https://fonts.googleapis.com/css2?family=Open+Sans:wght@400;600;700&family=Cinzel:wght@400&display=swap">
<style>
  :root {
    --brand-blue: #0455a3;
    --brand-blue-light: #1b8bd6;
    --silver: #d5d5d5;
    --paper: #ffffff;
    --ink: #1d1d1f;
    --tagline: #2d3f55;
    --backdrop: #e9eaec;
  }
  html, body {
    margin: 0;
    width: 1200px;
    height: 900px;
    overflow: hidden;
    background: var(--backdrop);
    font-family: "Open Sans", Arial, sans-serif;
  }
  .card {
    position: absolute;
    left: 150px;
    top: 193px;
    width: 900px;
    height: 514px;
    border-radius: 40px;
    overflow: hidden;
    box-shadow: 0 12px 34px rgba(0,0,0,0.18);
  }
  .card-shapes { position: absolute; inset: 0; }
  .holder {
    position: absolute;
    left: 52px;
    top: 92px;
    color: var(--paper);
  }
  .holder-name { font-size: 29px; font-weight: 700; margin: 0; line-height: 1.2; }
  .holder-title { font-size: 23px; font-weight: 400; margin: 0; line-height: 1.2; }
  .office-address {
    position: absolute;
    left: 88px;
    top: 212px;
    color: var(--paper);
    font-size: 18px;
    line-height: 1.45;
    font-style: normal;
  }
  .contact-list {
    position: absolute;
    left: 88px;
    top: 318px;
    margin: 0;
    padding: 0;
    list-style: none;
    color: var(--paper);
    font-size: 17px;
    line-height: 26px;
  }
  .contact-list li { display: flex; align-items: center; gap: 10px; white-space: nowrap; }
  .contact-list svg { width: 15px; height: 15px; flex: none; }
  .brand {
    position: absolute;
    left: 520px;
    top: 196px;
    width: 370px;
    display: flex;
    flex-direction: column;
    align-items: center;
  }
  .brand-lockup {
    display: flex;
    align-items: center;
    gap: 12px;
    white-space: nowrap;
  }
  .brand-dot {
    width: 30px;
    height: 30px;
    flex: none;
    border-radius: 50%;
    background: var(--brand-blue-light);
  }
  .brand-name {
    font-size: 30px;
    font-weight: 600;
    color: var(--ink);
    letter-spacing: 1px;
    text-transform: uppercase;
    line-height: 1;
  }
  .brand-tagline {
    margin: 44px 0 0;
    font-family: "Cinzel", Georgia, serif;
    font-size: 15px;
    letter-spacing: 2px;
    color: var(--tagline);
    white-space: nowrap;
  }
</style>
</head>
<body>
  <article class="card">
    <svg class="card-shapes" viewBox="0 0 900 514" width="900" height="514" aria-hidden="true">
      <defs>
        <radialGradient id="silver-face" cx="0.62" cy="0.35" r="0.75">
          <stop offset="0" stop-color="#ffffff"/>
          <stop offset="0.6" stop-color="#f1f1f1"/>
          <stop offset="1" stop-color="#d5d5d5"/>
        </radialGradient>
        <radialGradient id="blue-panel" cx="0.45" cy="0.5" r="0.7">
          <stop offset="0" stop-color="#1b8bd6"/>
          <stop offset="1" stop-color="#0455a3"/>
        </radialGradient>
      </defs>
      <rect class="silver-face" width="900" height="514" fill="url(#silver-face)"/>
      <path class="blue-panel" d="M0 0 H398 C322 120 330 380 512 514 H0 Z" fill="url(#blue-panel)"/>
      <path class="black-swoosh" d="M406 0 C336 120 344 380 522 514 L552 514 C382 392 374 140 432 0 Z" fill="#141414"/>
    </svg>

    <header class="holder">
      <h1 class="holder-name">Dorian Vellacott</h1>
      <p class="holder-title">Director</p>
    </header>

    <address class="office-address">214 Cedar Crest, 9th floor<br>Riverton Avenue RVT</address>

    <ul class="contact-list">
      <li>
        <svg viewBox="0 0 16 16" aria-label="Cell"><rect x="4" y="1" width="8" height="14" rx="1.5" fill="none" stroke="#fff" stroke-width="1.6"/><circle cx="8" cy="12.5" r="0.9" fill="#fff"/></svg>
        012 555 0147
      </li>
      <li>
        <svg viewBox="0 0 16 16" aria-label="Office"><path d="M3 1.5 L6 1.5 L7 5 L5.3 6.3 C6.2 8.2 7.8 9.8 9.7 10.7 L11 9 L14.5 10 L14.5 13 C14.5 14 13.6 14.6 12.6 14.5 C7 13.8 2.2 9 1.5 3.4 C1.4 2.4 2 1.5 3 1.5 Z" fill="#fff"/></svg>
        012 555 0148
      </li>
      <li>
        <svg viewBox="0 0 16 16" aria-label="Email"><rect x="1" y="3" width="14" height="10" fill="#fff"/><path d="M1 3 L8 9 L15 3" fill="none" stroke="#0c6cbd" stroke-width="1.3"/></svg>
        dorian@larkspurtalent.example
      </li>
      <li>
        <svg viewBox="0 0 16 16" aria-label="Website"><circle cx="8" cy="8" r="6.5" fill="none" stroke="#fff" stroke-width="1.4"/><ellipse cx="8" cy="8" rx="3" ry="6.5" fill="none" stroke="#fff" stroke-width="1.2"/><path d="M1.5 8 H14.5" stroke="#fff" stroke-width="1.2"/></svg>
        www.larkspurtalent.example
      </li>
    </ul>

    <section class="brand">
      <div class="brand-lockup">
        <span class="brand-dot"></span>
        <span class="brand-name">Larkspur Talent</span>
      </div>
      <p class="brand-tagline">BUILDING TEAMS THAT DELIVER</p>
    </section>
  </article>
</body>
</html>
```